Business card for law firm

Need business card for new law firm. Think confident, authoritative, conservative, but not stuffy or old-fashioned.

Contact Information for Business Card

Content for card - logo (uploaded), plus the following:

Paul Whitcombe (larger font)
Managing Partner (larger font, but not as large as name)
Level 9, 7 Ferris Lane
Sydney NSW 2000
Main Tel 02 9364 2710
Direct Tel 02 8472 3159
Email paul@qvlegal.com.au
www.qvlegal.com.au

Letterhead design should include logo plus:
Level 9, 7 Ferris Lane
Sydney NSW 2000
Tel 02 8472 3159
www.qvlegal.com.au

```html
<!DOCTYPE html>
<html lang="en">
<head>
<meta charset="UTF-8">
<title>Quayvale Legal – Business Card</title>
<link href="https://fonts.googleapis.com/css2?family=Cinzel:wght@500&family=Montserrat:wght@400&display=swap" rel="stylesheet">
<style>
  :root {
    --page-bg: #161616;
    --card-bg: #262626;
    --card-edge: #2c3486;
    --ink: #f2f2f2;
    --ink-soft: #d9d9d9;
    --ink-muted: #9a9a9a;
    --rule: #cfcfcf;
  }
  * { margin: 0; padding: 0; box-sizing: border-box; }
  html, body {
    width: 1200px;
    height: 900px;
    overflow: hidden;
    background: var(--page-bg);
  }
  .sheet {
    width: 1200px;
    height: 900px;
    display: flex;
    flex-direction: column;
    align-items: center;
    justify-content: center;
    gap: 60px;
  }
  .card {
    position: relative;
    width: 640px;
    height: 366px;
    background: var(--card-bg);
    border-bottom: 5px solid var(--card-edge);
    box-shadow: 0 18px 40px rgba(0,0,0,0.55);
  }
  .brand {
    display: flex;
    flex-direction: column;
    align-items: center;
    gap: 18px;
  }
  .brand-mark {
    width: 54px;
    height: 54px;
    background: var(--ink);
  }
  .brand-name {
    font-family: 'Cinzel', serif;
    font-weight: 500;
    font-size: 34px;
    letter-spacing: 2px;
    color: var(--ink);
    text-align: center;
    line-height: 1.1;
  }
  .card-front {
    display: flex;
    align-items: center;
    justify-content: center;
  }
  .card-front .brand-mark { background: var(--ink-muted); }
  .card-front .brand-name { color: var(--ink-muted); }
  .card-back {
    display: flex;
    align-items: center;
    padding: 0 40px 0 44px;
  }
  .card-back .brand { width: 250px; }
  .divider {
    width: 1px;
    height: 200px;
    background: var(--rule);
    margin: 0 30px 0 30px;
  }
  .contact {
    color: var(--ink-soft);
    font-family: 'Montserrat', sans-serif;
  }
  .person-name {
    font-family: 'Cinzel', serif;
    font-weight: 500;
    font-size: 23px;
    color: var(--ink);
    letter-spacing: 0.5px;
  }
  .person-role {
    font-size: 15px;
    margin-top: 2px;
    margin-bottom: 14px;
  }
  .address {
    font-size: 15px;
    line-height: 1.35;
    margin-bottom: 14px;
  }
  .details { list-style: none; }
  .details li {
    display: flex;
    align-items: center;
    gap: 12px;
    font-size: 15px;
    line-height: 1.6;
  }
  .details svg {
    width: 13px;
    height: 13px;
    flex: none;
    stroke: var(--ink-soft);
    fill: none;
    stroke-width: 1.6;
  }
</style>
</head>
<body>
<main class="sheet">
  <section class="card card-front" aria-label="Card front">
    <div class="brand">
      <span class="brand-mark"></span>
      <span class="brand-name">QUAYVALE LEGAL</span>
    </div>
  </section>

  <section class="card card-back" aria-label="Card back">
    <div class="brand">
      <span class="brand-mark"></span>
      <span class="brand-name">QUAYVALE LEGAL</span>
    </div>
    <span class="divider"></span>
    <div class="contact">
      <p class="person-name">PAUL WHITCOMBE</p>
      <p class="person-role">Managing Partner</p>
      <p class="address">Level 9, 7 Ferris Lane<br>Sydney NSW 2000</p>
      <ul class="details">
        <li>
          <svg viewBox="0 0 16 16" aria-hidden="true"><path d="M4 1.5l2.5 3-1.5 2c1 2 2.5 3.5 4.5 4.5l2-1.5 3 2.5-1.5 2.5C7 14 2 9 1.5 3z"/></svg>
          02 9364 2710
        </li>
        <li>
          <svg viewBox="0 0 16 16" aria-hidden="true"><rect x="4" y="1" width="8" height="14" rx="1.5"/><line x1="7" y1="12.5" x2="9" y2="12.5"/></svg>
          02 8472 3159
        </li>
        <li>
          <svg viewBox="0 0 16 16" aria-hidden="true"><rect x="1" y="3" width="14" height="10" rx="1"/><path d="M1.5 3.5L8 9l6.5-5.5"/></svg>
          paul@qvlegal.com.au
        </li>
        <li>
          <svg viewBox="0 0 16 16" aria-hidden="true"><circle cx="8" cy="8" r="6.5"/><ellipse cx="8" cy="8" rx="3" ry="6.5"/><line x1="1.5" y1="8" x2="14.5" y2="8"/></svg>
          www.qvlegal.com.au
        </li>
      </ul>
    </div>
  </section>
</main>
</body>
</html>
```